Simple and Clean business card design

We would like the design to be simple clean and to incorporate our colors.

We are open to your design and talent, we have the dots in our logo as we think of it as data points and we connect data points for people.

We are open to see the great creative and clean design you bring to the table

Contact Information for Business Card

please include: name, position, email, phone and website

Font styles to use
Sans Serif

Requirements
Must have
• my colors incorporated, simplicity
Nice to have
• lots of white space, simplicity
Should not have
• complexicity/ complex art

```html
<!DOCTYPE html>
<html lang="en">
<head>
<meta charset="utf-8">
<title>Nectra Business Card</title>
<link rel="stylesheet" href="https://fonts.googleapis.com/css2?family=Arimo:wght@400;700&display=swap">
<style>
  :root {
    --backdrop: #e4e3e0;
    --card: #2b2b2c;
    --card-edge: #2f5fb8;
    --ink-light: #f2f2f2;
    --ink-muted: #d4d4d4;
    --brand-blue: #3f7be0;
    --brand-green: #2f9a4a;
    --brand-yellow: #e2aa12;
    --emboss: #3a3a3b;
  }
  * { box-sizing: border-box; margin: 0; padding: 0; }
  html, body {
    width: 1200px; height: 801px; overflow: hidden;
    background: var(--backdrop);
    font-family: "Arimo", Arial, sans-serif;
  }
  .canvas {
    width: 1200px; height: 801px;
    display: flex; align-items: center; justify-content: center; gap: 40px;
  }
  .card {
    position: relative;
    width: 540px; height: 309px;
    background: var(--card);
    border-bottom: 4px solid var(--card-edge);
    box-shadow: 0 10px 24px rgba(0,0,0,0.18);
    overflow: hidden;
  }
  .wordmark {
    display: flex; align-items: center; gap: 12px;
    font-weight: 700; letter-spacing: 1px; line-height: 1;
  }
  .wordmark-dot { width: 16px; height: 16px; border-radius: 50%; flex: none; }

  /* back side */
  .card-back { display: flex; align-items: center; justify-content: center; }
  .card-back .wordmark { font-size: 76px; color: var(--emboss); }
  .card-back .wordmark-dot { width: 22px; height: 22px; background: var(--emboss); }

  /* front side */
  .card-front .wordmark {
    position: absolute; right: 40px; top: 46px;
    font-size: 60px; color: var(--ink-light);
  }
  .card-front .wordmark-dot { width: 18px; height: 18px; background: var(--brand-blue); }

  .identity { position: absolute; left: 36px; top: 150px; }
  .person-name { font-size: 24px; font-weight: 700; color: var(--brand-blue); line-height: 1.1; }
  .person-role { margin-top: 4px; font-size: 15px; color: var(--ink-muted); }

  .divider {
    position: absolute; left: 36px; right: 40px; top: 204px;
    height: 1px; background: var(--ink-muted);
  }

  .address {
    position: absolute; right: 40px; top: 218px;
    text-align: right; font-size: 14px; line-height: 1.35; color: var(--ink-muted);
  }

  .contacts {
    position: absolute; left: 36px; top: 216px;
    list-style: none; font-size: 15px; color: var(--ink-light);
  }
  .contacts li { display: flex; align-items: center; gap: 10px; height: 24px; }
  .contacts svg { width: 14px; height: 14px; flex: none; }
</style>
</head>
<body>
<main class="canvas">
  <section class="card card-back" aria-label="Card back">
    <div class="wordmark"><span class="wordmark-dot"></span><span>nectra</span></div>
  </section>

  <section class="card card-front" aria-label="Card front">
    <div class="wordmark"><span class="wordmark-dot"></span><span>nectra</span></div>

    <div class="identity">
      <p class="person-name">Daniel Reyes</p>
      <p class="person-role">Manager</p>
    </div>

    <div class="divider"></div>

    <p class="address">Your address, city<br>state, ZIP 0000</p>

    <ul class="contacts">
      <li>
        <svg viewBox="0 0 24 24" aria-hidden="true"><path fill="var(--brand-blue)" d="M6.6 10.8c1.4 2.8 3.8 5.1 6.6 6.6l2.2-2.2c.3-.3.7-.4 1-.2 1.1.4 2.3.6 3.6.6.6 0 1 .4 1 1V20c0 .6-.4 1-1 1C10.6 21 3 13.4 3 4c0-.6.4-1 1-1h3.5c.6 0 1 .4 1 1 0 1.3.2 2.5.6 3.6.1.3 0 .7-.2 1L6.6 10.8z"/></svg>
        <span>555-014-7730</span>
      </li>
      <li>
        <svg viewBox="0 0 24 24" aria-hidden="true"><rect x="3" y="6" width="18" height="12" rx="1" fill="none" stroke="var(--brand-green)" stroke-width="2"/><path d="M3 7l9 6 9-6" fill="none" stroke="var(--brand-green)" stroke-width="2"/></svg>
        <span>hello@nectra-data.com</span>
      </li>
      <li>
        <svg viewBox="0 0 24 24" aria-hidden="true"><g fill="none" stroke="var(--brand-yellow)" stroke-width="2"><circle cx="12" cy="12" r="9"/><path d="M3 12h18M12 3c3 3 3 15 0 18M12 3c-3 3-3 15 0 18"/></g></svg>
        <span>www.nectra-data.com</span>
      </li>
    </ul>
  </section>
</main>
</body>
</html>
```